Poster/flyer design needed for Choral Concert

Please include the following text:<br/>Title of Event: Voices in Bloom!<br/>Subtitle: A Choral Festival of Song to celebrate Kinship Fortnight<br/>Merrigang choirs come together to share their unique and beautiful music.<br/>Date: Sat March 21st 2020<br/>Time: 2pm - 4pm<br/>Venue: Pelmont Hall of Crafts<br/>Tickets: $10 each. Proceeds to Farmhand Trust & WBR Fire Corps<br/>Hosted By Lifted Tunes<br/>Featuring:<br/>Birrulee Unaccompanied Ladies' Choir<br/>Bread of Joy<br/>Merrigang Township Choir<br/>Chant Together<br/>* design required for A4 poster and DL flyer (may be modified)<br/>* Please use orange as the main colour<br/>* The Kinship fortnight logo must be included (see attached - either is fine). The frame may be useful as well.<br/>* Please include musical images<br/>* Visit kinshipfortnight.example.au for info on Kinship Fortnight

Target Market(s)

music-lovers, community-minded people, residents of the area, probably 30 + age

Industry/Entity Type

Entertainment

Font styles to use
Serif
Sans Serif

Colors
f78f20
ffffff

Requirements
Must have
• Orange colour
• Kinship logo
• required text
Nice to have
• A musical theme
Should not have
• writing should not be too small and difficult to read

```html
<!DOCTYPE html>
<html lang="en">
<head>
<meta charset="utf-8">
<title>Voices in Bloom! – Kinship Fortnight Choral Festival</title>
<link href="https://fonts.googleapis.com/css2?family=Bebas+Neue&family=Oswald:wght@400;700&family=Great+Vibes&family=Quicksand:wght@400;700&display=swap" rel="stylesheet">
<style>
  :root {
    --orange: #f78f20;
    --orange-deep: #e07a1c;
    --brown-top: #7a4a22;
    --rust: #6b2a12;
    --panel: #6a2514;
    --white: #ffffff;
    --ink: #111111;
  }
  * { margin: 0; padding: 0; box-sizing: border-box; }
  html, body { width: 871px; height: 1200px; overflow: hidden; }
  body { background: var(--white); }
  .poster {
    position: relative;
    width: 871px;
    height: 1200px;
    overflow: hidden;
    background: linear-gradient(180deg, #a8672d 0%, #e2952f 45%, var(--orange) 62%, #f59a2a 100%);
  }
  .hero-photo {
    position: absolute;
    left: 0; top: 0;
    width: 871px; height: 560px;
    background:
      radial-gradient(ellipse 420px 300px at 640px 220px, rgba(255,226,150,0.85), rgba(255,210,120,0) 70%),
      linear-gradient(180deg, rgba(120,70,30,0.55) 0%, rgba(200,120,40,0.25) 70%, rgba(247,143,32,0) 100%);
  }
  .brand-mark {
    position: absolute;
    left: 79px; top: 82px;
    font-family: "Oswald", sans-serif;
    font-weight: 400;
    font-size: 30px;
    color: var(--white);
    text-transform: uppercase;
    letter-spacing: 0.5px;
  }
  .event-title { font-weight: normal; }
  .title-block {
    position: absolute;
    left: 0; width: 871px; top: 409px;
    text-align: center;
    font-family: "Oswald", sans-serif;
    font-weight: 700;
    font-size: 228px;
    line-height: 1;
    letter-spacing: 14px;
    padding-left: 14px;
    background: linear-gradient(180deg, #7c3d1a 0%, #c4551f 60%, #e0672a 100%);
    -webkit-background-clip: text;
    background-clip: text;
    color: transparent;
    z-index: 1;
  }
  .title-script {
    position: absolute;
    left: 0; width: 871px; top: 300px;
    text-align: center;
    font-family: "Great Vibes", cursive;
    font-size: 150px;
    line-height: 1.2;
    color: var(--white);
    z-index: 2;
    padding-right: 60px;
  }
  .subtitle {
    position: absolute;
    left: 0; width: 871px; top: 650px;
    text-align: center;
    font-family: "Bebas Neue", sans-serif;
    font-size: 35px;
    line-height: 36px;
    color: var(--rust);
    white-space: nowrap;
  }
  .lineup {
    position: absolute;
    left: 60px; width: 372px; top: 808px;
    text-align: center;
    font-family: "Bebas Neue", sans-serif;
    color: var(--rust);
  }
  .lineup .label { font-size: 20px; line-height: 22px; }
  .lineup .host { font-size: 29px; line-height: 30px; margin-bottom: 22px; }
  .lineup ul { list-style: none; }
  .lineup li { font-size: 25px; line-height: 35px; white-space: nowrap; }
  .lineup li::before {
    content: "";
    display: inline-block;
    border-left: 6px solid var(--rust);
    border-top: 5px solid transparent;
    border-bottom: 5px solid transparent;
    margin-right: 8px;
    vertical-align: 5px;
  }
  .details-panel {
    position: absolute;
    left: 445px; top: 795px;
    width: 357px; height: 182px;
    background: var(--panel);
    display: flex; flex-direction: column; justify-content: center;
    text-align: center;
    font-family: "Bebas Neue", sans-serif;
    font-size: 39px;
    line-height: 38px;
    color: var(--white);
  }
  .details-panel sup { font-size: 20px; vertical-align: 16px; }
  .tickets {
    position: absolute;
    left: 445px; width: 357px; top: 1002px;
    text-align: center;
    font-family: "Quicksand", sans-serif;
    color: var(--rust);
  }
  .tickets .price { font-weight: 700; font-size: 25px; line-height: 28px; color: #3a1608; }
  .tickets .cause { font-size: 15px; line-height: 18px; }
  .footer-band {
    position: absolute;
    left: 0; top: 1109px;
    width: 871px; height: 91px;
    background: var(--white);
    display: flex; align-items: center; justify-content: space-between;
    padding: 0 100px 0 102px;
    font-family: "Oswald", sans-serif;
    font-weight: 400;
    color: var(--ink);
  }
  .gov-partner { display: flex; align-items: center; gap: 8px; font-size: 11px; line-height: 14px; }
  .gov-partner .dot { width: 22px; height: 22px; border-radius: 50%; background: var(--ink); }
  .tagline { font-size: 22px; text-transform: uppercase; letter-spacing: 1px; }
  .hashtag { font-size: 22px; }
</style>
</head>
<body>
<main class="poster">
  <div class="hero-photo" role="img" aria-label="Soft-focus photograph of an open book of choral sheet music"></div>
  <div class="brand-mark">Kinship Fortnight</div>

  <h1 class="event-title">
    <span class="title-block">BLOOM</span>
    <span class="title-script">Voices in</span>
  </h1>

  <p class="subtitle">
    A choral festival of song to celebrate Kinship Fortnight<br>
    Merrigang choirs come together to share<br>
    their unique and beautiful music.
  </p>

  <section class="lineup">
    <div class="label">Hosted by:</div>
    <div class="host">Lifted Tunes</div>
    <div class="label">Featuring:</div>
    <ul>
      <li>Birrulee Unaccompanied Ladies' Choir</li>
      <li>Bread of Joy</li>
      <li>Merrigang Township Choir</li>
      <li>Chant Together</li>
    </ul>
  </section>

  <section class="details-panel">
    <div>Saturday, March 21<sup>st</sup></div>
    <div>Pelmont Hall of Crafts</div>
    <div>2pm - 4pm</div>
  </section>

  <section class="tickets">
    <div class="price">TICKETS: $10 EACH</div>
    <div class="cause">Proceeds to Farmhand Trust<br>&amp; WBR Fire Corps</div>
  </section>

  <footer class="footer-band">
    <div class="gov-partner">
      <span class="dot"></span>
      <span>Commonwealth Office<br>of Community Affairs</span>
    </div>
    <div class="tagline">All Are Welcome</div>
    <div class="hashtag">#kinshipfortnight</div>
  </footer>
</main>
</body>
</html>
```